New Business Card Design Project

We require a business card design for Vexalund, a newly established Indian company.
Our focus is on the development, manufacturing, and export of a diverse array of pharmaceutical products on a global scale. The card should convey a professional appearance, as our primary markets are in Africa, China, and Southeast Asian nations.
We envision a two-sided business card, with the reverse side dedicated to a logo set against a solid color or an elegantly designed pattern. The corners should be rounded. We would appreciate seeing both horizontal and vertical design options. We trust the designer to utilize their expertise in creating this design.

The content for the business card is included in the attached Word file.

Target Market(s)

Our primary markets are in Africa, China, and Southeast Asian, Latin America, Maldives, Sri Lanka

Industry/Entity Type

Pharmaceutical Manufacturing and Export

Contact Information for Business Card

Colors

Designer to choose colors to be used in the design.

Requirements
Must have
• The reverse side of the business card features solely the logo along with the tagline, "Care Beyond Borders."
Should not have
• The logo should not exceed two instances, encompassing both the front and back sides of the card.

```html
<!DOCTYPE html>
<html lang="en">
<head>
<meta charset="utf-8">
<title>Vexalund Business Card</title>
<link rel="stylesheet" href="https://fonts.googleapis.com/css2?family=Poppins:wght@500;600&family=Roboto:wght@400&display=swap">
<style>
  :root {
    --stage: #2b2b2d;
    --brand-blue: #27a8e0;
    --brand-red: #f0604a;
    --ink: #333333;
    --card-white: #ffffff;
    --divider: #9a9a9a;
  }
  html, body {
    margin: 0;
    padding: 0;
    width: 1200px;
    height: 874px;
    overflow: hidden;
    background: var(--stage);
  }
  .canvas {
    position: relative;
    width: 1200px;
    height: 874px;
  }
  .card {
    position: absolute;
    left: 280px;
    width: 640px;
    height: 366px;
    border-radius: 26px;
    overflow: hidden;
    box-shadow: 0 10px 30px rgba(0,0,0,0.45);
  }
  .wordmark {
    display: flex;
    align-items: center;
    gap: 14px;
    font-family: "Poppins", sans-serif;
    font-weight: 600;
    letter-spacing: 0.5px;
    line-height: 1;
    white-space: nowrap;
  }
  .wordmark-dot {
    border-radius: 50%;
    background: var(--brand-red);
    flex: none;
  }
  /* Back side */
  .card-back {
    top: 50px;
    background: var(--brand-blue);
  }
  .card-back .wordmark {
    position: absolute;
    left: 0;
    right: 0;
    top: 168px;
    justify-content: center;
    color: var(--card-white);
    font-size: 62px;
  }
  .card-back .wordmark-dot {
    width: 24px;
    height: 24px;
  }
  .tagline {
    position: absolute;
    left: 0;
    right: 0;
    top: 290px;
    margin: 0;
    text-align: center;
    font-family: "Roboto", sans-serif;
    font-size: 15px;
    color: var(--card-white);
  }
  /* Front side */
  .card-front {
    top: 458px;
    background: var(--card-white);
  }
  .front-brand {
    position: absolute;
    left: 0;
    top: 0;
    width: 330px;
    height: 300px;
    display: flex;
    align-items: center;
    justify-content: center;
  }
  .card-front .wordmark {
    color: var(--brand-blue);
    font-size: 48px;
  }
  .card-front .wordmark-dot {
    width: 20px;
    height: 20px;
  }
  .front-divider {
    position: absolute;
    left: 332px;
    top: 58px;
    width: 2px;
    height: 196px;
    background: linear-gradient(to bottom, rgba(154,154,154,0), var(--divider) 30%, var(--divider) 70%, rgba(154,154,154,0));
  }
  .contact-block {
    position: absolute;
    left: 360px;
    top: 60px;
    font-family: "Roboto", sans-serif;
    color: var(--ink);
  }
  .person-name {
    margin: 0;
    font-family: "Poppins", sans-serif;
    font-weight: 600;
    font-size: 26px;
    color: var(--brand-blue);
    line-height: 1.1;
    white-space: nowrap;
  }
  .person-role {
    margin: 0 0 14px;
    font-size: 14px;
    color: var(--brand-red);
  }
  .address {
    margin: 0 0 10px;
    font-size: 14px;
    line-height: 1.35;
  }
  .contact-list {
    list-style: none;
    margin: 0;
    padding: 0;
    font-size: 14px;
  }
  .contact-list li {
    display: flex;
    align-items: center;
    gap: 9px;
    line-height: 22px;
  }
  .contact-icon {
    width: 13px;
    height: 13px;
    flex: none;
  }
  .edge-stripe {
    position: absolute;
    left: 0;
    right: 0;
    bottom: 40px;
    height: 4px;
    background: var(--brand-red);
  }
  .edge-band {
    position: absolute;
    left: 0;
    right: 0;
    bottom: 0;
    height: 34px;
    background: var(--brand-blue);
  }
</style>
</head>
<body>
<main class="canvas">

  <section class="card card-back" aria-label="Card reverse side">
    <div class="wordmark">
      <span class="wordmark-dot"></span>
      <span>Vexalund</span>
    </div>
    <p class="tagline">Care Beyond Borders</p>
  </section>

  <section class="card card-front" aria-label="Card front side">
    <div class="front-brand">
      <div class="wordmark">
        <span class="wordmark-dot"></span>
        <span>Vexalund</span>
      </div>
    </div>

    <div class="front-divider"></div>

    <div class="contact-block">
      <h1 class="person-name">Ravin K. Solanki</h1>
      <p class="person-role">CEO</p>
      <p class="address">12, Nilgiri Nagar, Pune<br>411014, India</p>
      <ul class="contact-list">
        <li>
          <svg class="contact-icon" viewBox="0 0 16 16" aria-hidden="true">
            <path fill="#27a8e0" d="M3.6 1.2l2.3 2.6-1.3 1.8c.9 2.2 2.6 3.9 4.8 4.8l1.8-1.3 2.6 2.3-1.4 2.4C7.1 13.6 2.4 8.9 1.2 3z"/>
          </svg>
          <span>+919812045371</span>
        </li>
        <li>
          <svg class="contact-icon" viewBox="0 0 16 16" aria-hidden="true">
            <rect x="1" y="3" width="14" height="10" rx="1" fill="#27a8e0"/>
            <path d="M1.5 3.8L8 9l6.5-5.2" fill="none" stroke="#ffffff" stroke-width="1.4"/>
          </svg>
          <span>rsolanki@vexalund.com</span>
        </li>
        <li>
          <svg class="contact-icon" viewBox="0 0 16 16" aria-hidden="true">
            <circle cx="8" cy="8" r="7" fill="#27a8e0"/>
            <path d="M1 8h14M8 1c-2.5 2.5-2.5 11.5 0 14M8 1c2.5 2.5 2.5 11.5 0 14" fill="none" stroke="#ffffff" stroke-width="1"/>
          </svg>
          <span>www.vexalund.com</span>
        </li>
      </ul>
    </div>

    <div class="edge-stripe"></div>
    <div class="edge-band"></div>
  </section>

</main>
</body>
</html>
```